Diagnostic MRI imaging center needs a website

We need a website design for a new diagnositic MRI imaging center.
Please refer to the attachment of guideline.

Coding

Coded - Design and coding required

Number of Pages Required

5+ page

Requirements
Must have
• Corvane Tessaly MRI scanner images, NOT CT scanner images. Thanks
Nice to have
• Please only show MRI scanner images, not CT and other modalities
Should not have
• CT and other modalities scanner images

```html
<!DOCTYPE html>
<html lang="en">
<head>
<meta charset="utf-8">
<title>Nuvela Imaging – Innovative Diagnostic Imaging</title>
<link href="https://fonts.googleapis.com/css2?family=Poppins:wght@400;500;600;700&display=swap" rel="stylesheet">
<style>
:root{
  --teal:#13aba3;
  --navy:#3b3f56;
  --ink:#1f1f24;
  --light:#efefef;
  --footer:#121212;
  --white:#ffffff;
}
*{box-sizing:border-box;margin:0;padding:0}
html,body{width:1200px;height:4919px;overflow:hidden}
body{font-family:"Poppins",sans-serif;color:var(--ink);background:var(--white);position:relative}
.section{position:absolute;left:0;width:1200px}
.btn{position:absolute;background:var(--teal);color:var(--white);border-radius:20px;font-size:15px;font-weight:500;display:flex;align-items:center;justify-content:center;letter-spacing:.3px;white-space:nowrap}
.heading{position:absolute;left:0;width:1200px;text-align:center;font-weight:600;font-size:42px;letter-spacing:.5px}
.heading .accent{color:var(--teal)}
.photo{position:absolute}

/* top bar */
.topbar{top:0;height:42px;background:var(--navy);color:var(--white);font-size:11px}
.topbar .item{position:absolute;top:13px;display:flex;align-items:center;gap:6px;white-space:nowrap}

/* nav */
.nav{top:42px;height:107px;background:var(--white)}
.brand-mark{position:absolute;left:58px;top:36px;display:flex;align-items:center;gap:10px;font-size:24px;font-weight:600;color:var(--ink);white-space:nowrap}
.brand-mark i{display:block;width:26px;height:26px;border-radius:50%;background:var(--teal)}
.menu a{position:absolute;top:48px;font-size:15px;font-weight:500;color:var(--ink);text-decoration:none;white-space:nowrap}
.menu a.active{color:var(--teal)}
.menu a.active::after{content:"";position:absolute;left:0;right:0;bottom:-12px;height:2px;background:var(--teal)}

/* hero */
.hero{top:149px;height:562px;background:linear-gradient(100deg,#4a5a74 0%,#7d8ba0 40%,#9aa6b6 70%,#c3c9d1 100%);overflow:hidden}
.hero .shade{position:absolute;inset:0;background:rgba(45,55,80,.45)}
.hero-kicker{position:absolute;top:84px;left:0;width:1200px;text-align:center;color:var(--teal);font-size:31px;font-weight:500}
.hero-title{position:absolute;top:128px;left:0;width:1220px;text-align:center;color:var(--white);font-size:62px;font-weight:700;line-height:76px;letter-spacing:1px}

/* about */
.about{top:711px;height:508px}
.about h2{position:absolute;left:583px;top:128px;font-size:42px;font-weight:600;white-space:nowrap}
.about h2 span{color:var(--teal)}
.about p{position:absolute;left:587px;width:480px;font-size:13.5px;line-height:24px;color:#3a3a40}

/* why */
.why{top:1219px;height:507px;background:var(--teal);color:var(--white)}
.why .heading{top:50px;color:var(--white)}
.feature{position:absolute;width:330px;text-align:center}
.feature h3{font-size:19px;font-weight:500;margin-top:10px;letter-spacing:.3px}
.feature p{font-size:14px;line-height:26px;margin-top:12px}

/* services */
.services{top:1726px;height:816px}
.service{position:absolute;width:260px;text-align:center}
.service .ring{width:180px;height:180px;margin:0 auto;border-radius:50%;border:4px solid var(--teal);overflow:hidden}
.service .ring div{width:100%;height:100%}
.service h4{margin-top:16px;font-size:18px;font-weight:600;letter-spacing:.3px}

/* specialists */
.specialists{top:2542px;height:428px;background:var(--teal)}
.specialists .heading{top:62px;color:var(--white)}
.doc{position:absolute;width:197px;height:145px;background:var(--white);border-radius:8px;text-align:center}
.doc .avatar{position:absolute;left:50%;top:-84px;margin-left:-58px;width:116px;height:116px;border-radius:50%;background:var(--white);overflow:hidden}
.doc .avatar div{width:100%;height:100%;background:radial-gradient(circle at 50% 45%,#e7cdb5 0%,#d8b89c 38%,#eef2f6 39%,#ffffff 100%)}
.doc h5{margin-top:44px;font-size:15px;font-weight:500;color:var(--teal);white-space:nowrap}
.doc p{font-size:9px;line-height:15px;color:#444;margin-top:4px;padding:0 10px}
.doc .go{position:absolute;left:50%;bottom:-14px;margin-left:-15px;width:30px;height:30px;border-radius:50%;background:var(--white);border:2px solid var(--teal);display:flex;align-items:center;justify-content:center}

/* testimonials */
.reviews{top:2970px;height:520px;background:var(--light)}
.reviews .heading{top:90px}
.review{position:absolute;top:199px;width:311px;height:223px;background:var(--white);border-radius:8px;box-shadow:0 2px 10px rgba(0,0,0,.06);text-align:center}
.review .stars{margin-top:22px;display:flex;justify-content:center;gap:4px}
.review p{font-size:11px;line-height:19px;color:#777;margin-top:14px;padding:0 28px}
.review .who{position:absolute;left:58px;top:160px;display:flex;align-items:center;gap:14px;text-align:left}
.review .pic{width:44px;height:44px;border-radius:50%;background:linear-gradient(160deg,#8a6d5c,#3d3230)}
.review .who b{display:block;font-size:12px;font-weight:500;color:#333;white-space:nowrap}
.review .who span{font-size:10px;color:#888}

/* appointment */
.appt{top:3490px;height:627px}
.appt .panel{position:absolute;left:673px;top:0;width:527px;height:627px;background:var(--teal)}
.appt h2{position:absolute;left:54px;top:92px;font-size:42px;font-weight:600;white-space:nowrap}
.appt h2 span{color:var(--teal)}
.contact{position:absolute;top:210px;width:200px}
.contact b{display:block;margin-top:12px;font-size:14px;font-weight:500}
.contact span{display:block;font-size:12px;line-height:20px;color:#666;margin-top:6px}
.map{position:absolute;left:52px;top:345px;width:607px;height:264px;background:linear-gradient(135deg,#e6efe2 0%,#dfe6ea 45%,#cfe0ee 70%,#e9ece4 100%)}
.form{position:absolute;left:745px;top:82px;width:396px;height:485px;background:var(--white)}
.form h3{position:absolute;left:38px;top:38px;font-size:21px;font-weight:500}
.form .intro{position:absolute;left:38px;top:80px;width:320px;font-size:10px;line-height:17px;color:#777}
.form label{position:absolute;font-size:11px;color:#333}
.form .field{position:absolute;height:36px;background:#f4f5f6;border-radius:2px;font-size:9px;color:#aaa;padding:11px 12px}
.form .send{position:absolute;left:38px;top:426px;width:320px;height:36px;background:#3aa79f;color:var(--white);font-size:11px;display:flex;align-items:center;justify-content:center}

/* insurance */
.insurance{top:4117px;height:397px}
.insurance .heading{top:60px}
.plan{position:absolute;top:166px;height:99px;background:var(--white);border:1px solid #f0f0f0;display:flex;align-items:center;justify-content:center;gap:10px;font-size:28px;font-weight:600;color:#4d5a8a;white-space:nowrap}
.plan i{width:18px;height:18px;background:currentColor;border-radius:50%;display:block}

/* footer */
.footer{top:4514px;height:405px;background:var(--footer);color:var(--white)}
.footer .brand{position:absolute;left:74px;top:84px;display:flex;align-items:center;gap:10px;font-size:23px;font-weight:600;color:var(--white);white-space:nowrap}
.footer .brand i{display:block;width:22px;height:22px;border-radius:50%;background:var(--teal)}
.footer .about-text{position:absolute;left:74px;top:178px;width:330px;font-size:13.5px;line-height:30px}
.footer h6{position:absolute;top:84px;font-size:21px;font-weight:500;color:var(--teal)}
.footer ul{position:absolute;top:138px;list-style:none}
.footer li{font-size:13.5px;line-height:22px;margin-bottom:17px;padding-left:26px;position:relative}
.footer li::before{content:"";position:absolute;left:0;top:8px;width:7px;height:7px;border-radius:50%;background:var(--teal)}
.footer .quick{position:absolute;left:928px;top:138px;width:240px}
.footer .quick div{position:relative;padding-left:38px;font-size:13.5px;line-height:26px;margin-bottom:14px}
.footer .quick svg{position:absolute;left:0;top:5px}
</style>
</head>
<body>

<!-- top bar -->
<div class="section topbar">
  <div class="item" style="left:641px">
    <svg width="14" height="14" viewBox="0 0 14 14"><circle cx="7" cy="7" r="7" fill="#fff"/><path d="M4.5 3.8l1.4-.3.7 1.8-.9.7c.5 1 1.2 1.7 2.2 2.2l.7-.9 1.8.7-.3 1.4c-3 .2-5.8-2.6-5.6-5.6z" fill="#3b3f56"/></svg>
    (555) 201 4470
  </div>
  <div class="item" style="left:786px">
    <svg width="14" height="14" viewBox="0 0 14 14"><circle cx="7" cy="7" r="7" fill="#fff"/><path d="M7 3a2.6 2.6 0 0 0-2.6 2.6C4.4 7.6 7 11 7 11s2.6-3.4 2.6-5.4A2.6 2.6 0 0 0 7 3zm0 3.6a1 1 0 1 1 0-2 1 1 0 0 1 0 2z" fill="#3b3f56"/></svg>
    4410 West Meridian Avenue Coral Springs, FL 33065
  </div>
</div>

<!-- navigation -->
<div class="section nav">
  <div class="brand-mark"><i></i>Nuvela Imaging</div>
  <nav class="menu">
    <a class="active" style="left:263px">HOME</a>
    <a style="left:368px">ABOUT</a>
    <a style="left:476px">SERVICES</a>
    <a style="left:607px">PATIENT RESOURCES</a>
    <a style="left:825px">BLOG</a>
  </nav>
  <div class="btn" style="left:929px;top:40px;width:218px;height:38px">REQUEST APPOINTMENT</div>
</div>

<!-- hero -->
<div class="section hero" role="img" aria-label="Radiographer preparing a patient on an MRI scanner table">
  <div class="shade"></div>
  <div class="hero-kicker">MRI CENTER</div>
  <div class="hero-title">INNOVATIVE<br>DIAGNOSTIC<br>IMAGING</div>
  <div class="btn" style="left:504px;top:394px;width:220px;height:34px">REQUEST APPOINTMENT</div>
</div>

<!-- about -->
<div class="section about">
  <div class="photo" role="img" aria-label="Doctor greeting a patient beside an MRI scanner" style="left:109px;top:82px;width:366px;height:366px;border-radius:50%;background:linear-gradient(135deg,#dfe5ea 0%,#c7d1d9 45%,#9fb0bd 100%);box-shadow:inset -14px -14px 0 var(--teal)"></div>
  <h2><span>ABOUT</span> MRI CENTER</h2>
  <p style="top:190px">Lorem ipsum dolor sit amet, consectetur adipiscing elit. Donec efficitur, enim bibendum volutpat dictum, tellus risus porttitor leo, eget eleifend enim metus eu sem. Ut ipsum eros.</p>
  <p style="top:264px">Lorem ipsum dolor sit amet, consectetur adipiscing elit. Donec efficitur, enim bibendum volutpat dictum, tellus risus porttitor leo, eget eleifend enim metus eu sem. Ut ipsum eros.</p>
  <div class="btn" style="left:587px;top:359px;width:220px;height:36px">MORE ABOUT US</div>
</div>

<!-- why choose us -->
<div class="section why">
  <div class="heading">WHY CHOOSE US</div>
  <div class="feature" style="left:97px;top:178px">
    <svg width="80" height="80" viewBox="0 0 80 80" fill="none" stroke="#fff" stroke-width="2"><rect x="44" y="8" width="26" height="18" rx="2"/><path d="M49 20l4-5 4 3 5-6"/><circle cx="30" cy="44" r="18"/><circle cx="30" cy="44" r="8"/><path d="M10 66h56M14 60h44l6 6"/><path d="M57 26v8"/></svg>
    <h3>ADVANCED TECHNOLOGY</h3>
    <p>Lorem ipsum dolor sit amet, consectetur adipiscing elit. Donec efficitur, enim bibendum volutpat dictum.</p>
  </div>
  <div class="feature" style="left:445px;top:178px">
    <svg width="80" height="80" viewBox="0 0 80 80" fill="none" stroke="#fff" stroke-width="2"><circle cx="40" cy="30" r="22"/><circle cx="40" cy="30" r="12"/><path d="M18 52h44v8H18zM28 60v12M52 60v12M40 18v6"/></svg>
    <h3>PATIENT COMFORT</h3>
    <p>Lorem ipsum dolor sit amet, consectetur adipiscing elit. Donec efficitur, enim bibendum volutpat dictum.</p>
  </div>
  <div class="feature" style="left:785px;top:178px">
    <svg width="80" height="80" viewBox="0 0 80 80" fill="none" stroke="#fff" stroke-width="2"><circle cx="40" cy="24" r="12"/><path d="M18 74V60c0-9 8-15 22-15s22 6 22 15v14z"/><path d="M32 46l8 14 8-14M30 50v10a4 4 0 0 0 8 0"/></svg>
    <h3>QUALIFIED EXPERTS</h3>
    <p>Lorem ipsum dolor sit amet, consectetur adipiscing elit. Donec efficitur, enim bibendum volutpat dictum.</p>
  </div>
</div>

<!-- services -->
<div class="section services">
  <div class="heading" style="top:62px"><span class="accent">OUR</span> SERVICES</div>
  <div class="service" style="left:132px;top:180px"><div class="ring"><div role="img" aria-label="Patient lying on a scanner table" style="background:linear-gradient(160deg,#e9eef1,#b8c6cf)"></div></div><h4>CT SCAN</h4></div>
  <div class="service" style="left:459px;top:180px"><div class="ring"><div role="img" aria-label="Clinician performing an ultrasound exam" style="background:linear-gradient(160deg,#4d5a63,#1f2a31)"></div></div><h4>ULTRASOUND</h4></div>
  <div class="service" style="left:785px;top:180px"><div class="ring"><div role="img" aria-label="Brain scan images on a monitor" style="background:linear-gradient(160deg,#3e5a66,#14262e)"></div></div><h4>TOMOGRAPHY</h4></div>
  <div class="service" style="left:132px;top:438px"><div class="ring"><div role="img" aria-label="Doctor reviewing an X-ray film" style="background:linear-gradient(160deg,#e7ebee,#7c8b96)"></div></div><h4>DIGITAL X-RAY</h4></div>
  <div class="service" style="left:459px;top:438px"><div class="ring"><div role="img" aria-label="Brain scan slices on a light board" style="background:linear-gradient(160deg,#5a666e,#111a1f)"></div></div><h4>TBI</h4></div>
  <div class="service" style="left:785px;top:438px"><div class="ring"><div role="img" aria-label="Patient at a mammography unit" style="background:linear-gradient(160deg,#f0ece6,#b9b3ac)"></div></div><h4>Mammography</h4></div>
  <div class="btn" style="left:486px;top:731px;width:216px;height:34px">VIEW ALL SERVICES</div>
</div>

<!-- specialists -->
<div class="section specialists">
  <div class="heading">OUR SPECIALISTS</div>
  <div class="doc" style="left:132px;top:214px">
    <div class="avatar"><div role="img" aria-label="Portrait of a specialist physician"></div></div>
    <h5>Daniel Harwick, M.D.</h5>
    <p>Lorem ipsum dolor sit amet, consectetur adipiscing elit. Donec efficitur.</p>
    <div class="go"><svg width="14" height="14" viewBox="0 0 14 14"><path d="M12 2L2 6.5l4.5 1L7.5 12z" fill="none" stroke="#13aba3" stroke-width="1.6" stroke-linejoin="round"/></svg></div>
  </div>
  <div class="doc" style="left:493px;top:214px">
    <div class="avatar"><div role="img" aria-label="Portrait of a specialist physician"></div></div>
    <h5>Daniel Harwick, M.D.</h5>
    <p>Lorem ipsum dolor sit amet, consectetur adipiscing elit. Donec efficitur.</p>
    <div class="go"><svg width="14" height="14" viewBox="0 0 14 14"><path d="M12 2L2 6.5l4.5 1L7.5 12z" fill="none" stroke="#13aba3" stroke-width="1.6" stroke-linejoin="round"/></svg></div>
  </div>
  <div class="doc" style="left:864px;top:214px">
    <div class="avatar"><div role="img" aria-label="Portrait of a specialist physician"></div></div>
    <h5>Daniel Harwick, M.D.</h5>
    <p>Lorem ipsum dolor sit amet, consectetur adipiscing elit. Donec efficitur.</p>
    <div class="go"><svg width="14" height="14" viewBox="0 0 14 14"><path d="M12 2L2 6.5l4.5 1L7.5 12z" fill="none" stroke="#13aba3" stroke-width="1.6" stroke-linejoin="round"/></svg></div>
  </div>
</div>

<!-- testimonials -->
<div class="section reviews">
  <div class="heading"><span class="accent">WHAT</span> PATIENT SAYS</div>
  <div class="review" style="left:96px">
    <div class="stars"><svg width="90" height="12" viewBox="0 0 90 12"><g fill="#13aba3"><path id="st" d="M6 0l1.8 3.9 4.2.4-3.2 2.8 1 4.1L6 9.1 2.2 11.2l1-4.1L0 4.3l4.2-.4z"/><use href="#st" x="19"/><use href="#st" x="38"/><use href="#st" x="57"/><use href="#st" x="76"/></g></svg></div>
    <p>Molestie odio inceptos adipiscing dui dictum. Sodales aptent hac tristique integer nullam in vestibulum. Hac feugiat placerat laoreet fames pharetra pede imperdiet sodales in.</p>
    <div class="who"><div class="pic" role="img" aria-label="Patient photo"></div><div><b>Marcus T. Fenlow</b><span>CEO of Lumenfield</span></div></div>
  </div>
  <div class="review" style="left:438px">
    <div class="stars"><svg width="90" height="12" viewBox="0 0 90 12"><g fill="#13aba3"><use href="#st"/><use href="#st" x="19"/><use href="#st" x="38"/><use href="#st" x="57"/><use href="#st" x="76"/></g></svg></div>
    <p>Molestie odio inceptos adipiscing dui dictum. Sodales aptent hac tristique integer nullam in vestibulum. Hac feugiat placerat laoreet fames pharetra pede imperdiet sodales in.</p>
    <div class="who"><div class="pic" role="img" aria-label="Patient photo" style="background:linear-gradient(160deg,#d9b9a3,#8d6b57)"></div><div><b>Leona R. Vastel</b><span>Manager</span></div></div>
  </div>
  <div class="review" style="left:778px">
    <div class="stars"><svg width="90" height="12" viewBox="0 0 90 12"><g fill="#13aba3"><use href="#st"/><use href="#st" x="19"/><use href="#st" x="38"/><use href="#st" x="57"/><use href="#st" x="76"/></g></svg></div>
    <p>Molestie odio inceptos adipiscing dui dictum. Sodales aptent hac tristique integer nullam in vestibulum. Hac feugiat placerat laoreet fames pharetra pede imperdiet sodales in.</p>
    <div class="who"><div class="pic" role="img" aria-label="Patient photo" style="background:linear-gradient(160deg,#6f6a66,#2b2826)"></div><div><b>Owen P. Garrity</b><span>Accounting</span></div></div>
  </div>
</div>

<!-- appointment -->
<div class="section appt">
  <div class="panel"></div>
  <h2><span>GET</span> APPOINTMENT</h2>
  <div class="contact" style="left:52px">
    <svg width="22" height="28" viewBox="0 0 22 28" fill="none" stroke="#13aba3" stroke-width="2"><path d="M11 2a8 8 0 0 0-8 8c0 6 8 14 8 14s8-8 8-14a8 8 0 0 0-8-8z"/><circle cx="11" cy="10" r="3"/><path d="M4 26h14"/></svg>
    <b>Headquarters</b><span>512 Birch Ln, Eastfield, TX<br>75001</span>
  </div>
  <div class="contact" style="left:267px">
    <svg width="26" height="26" viewBox="0 0 26 26" fill="none" stroke="#13aba3" stroke-width="2"><path d="M6 3l4 1 1 5-3 2a13 13 0 0 0 7 7l2-3 5 1 1 4c-9 3-20-8-17-17z"/><path d="M15 3a8 8 0 0 1 8 8M15 7a4 4 0 0 1 4 4"/></svg>
    <b>Call Us</b><span>+1555.310.4482<br>+1555.310.4480</span>
  </div>
  <div class="contact" style="left:481px">
    <svg width="28" height="22" viewBox="0 0 28 22" fill="none" stroke="#13aba3" stroke-width="2"><rect x="2" y="2" width="24" height="18" rx="1"/><path d="M2 3l12 9 12-9"/></svg>
    <b>Email Us</b><span>info@clinicmail.test<br>hello@clinicmail.test</span>
  </div>
  <div class="map" role="img" aria-label="Street map showing the clinic location"></div>
  <div class="form">
    <h3>Send us a message</h3>
    <div class="intro">Class dolor et facilisi nibh taciti efficitur egestas. Praesent in commodo fringilla hendrerit nulla lacinia.</div>
    <label style="left:38px;top:140px">Your Name</label>
    <label style="left:204px;top:140px">Phone</label>
    <div class="field" style="left:38px;top:158px;width:154px">Your name</div>
    <div class="field" style="left:204px;top:158px;width:154px">Phone number</div>
    <label style="left:38px;top:202px">Email Address</label>
    <label style="left:204px;top:202px">Subject</label>
    <div class="field" style="left:38px;top:220px;width:154px">Your email</div>
    <div class="field" style="left:204px;top:220px;width:154px">Subject</div>
    <label style="left:38px;top:264px">Message</label>
    <div class="field" style="left:38px;top:282px;width:320px;height:118px">Your message</div>
    <div class="send">Send Message</div>
  </div>
</div>

<!-- insurance -->
<div class="section insurance">
  <div class="heading"><span class="accent">INSURANCE</span> PLANS</div>
  <div class="plan" style="left:76px;width:245px;color:#6b6b6b">Silvergate</div>
  <div class="plan" style="left:336px;width:249px;color:#2c72b8;font-size:22px"><i></i>Clearpath Health</div>
  <div class="plan" style="left:598px;width:239px;color:#2f63a9">Meridane</div>
  <div class="plan" style="left:852px;width:247px;color:#8a8a8a;font-size:22px;letter-spacing:3px">HARBORLINE</div>
</div>

<!-- footer -->
<div class="section footer">
  <div class="brand"><i></i>Nuvela Imaging</div>
  <div class="about-text">Lorem ipsum dolor sit amet, consectetur adipiscing elit. Ut elit tellus, luctus nec ullamcorper mattis, pulvinar dapibus leo. Ut elit tellus, luctus nec ullamcorper mattis, pulvinar dapibus leo.</div>

  <h6 style="left:495px">Pages</h6>
  <ul style="left:495px">
    <li>Homepage</li><li>About Us</li><li>Our Services</li><li>Contact</li>
  </ul>

  <h6 style="left:700px">Information</h6>
  <ul style="left:700px;width:200px">
    <li>Term &amp; Condition</li><li>Privacy Police</li><li>Frequently Asked Question</li><li>Blog &amp; News</li>
  </ul>

  <h6 style="left:928px">Quick Contact</h6>
  <div class="quick">
    <div><svg width="18" height="16" viewBox="0 0 18 16" fill="none" stroke="#13aba3" stroke-width="1.5"><path d="M2 6c0-3 14-3 14 0v2h-4V6H6v2H2z"/><path d="M4 9h10l1 6H3z"/><circle cx="9" cy="12" r="1.5"/></svg>+555 718 204</div>
    <div><svg width="18" height="16" viewBox="0 0 18 16" fill="none" stroke="#13aba3" stroke-width="1.5"><path d="M1 3l5-2 6 2 5-2v12l-5 2-6-2-5 2zM6 1v12M12 3v12"/></svg>27 Harbor Row, Eastfield 4411</div>
    <div><svg width="18" height="16" viewBox="0 0 18 16" fill="none" stroke="#13aba3" stroke-width="1.5"><circle cx="9" cy="8" r="7"/><circle cx="9" cy="8" r="3"/><path d="M12 5v4a2 2 0 0 0 4 0"/></svg>frontdesk@clinicmail.test</div>
  </div>
</div>

</body>
</html>
```